Business Card Design Project

Looking to update our business cards. We have a logo with our slogan. We are an IT firm so we wouldlike a modern look.

Industry/Entity Type

Business

```html
<!DOCTYPE html>
<html lang="en">
<head>
<meta charset="utf-8">
<title>Renewa Business Card</title>
<link rel="stylesheet" href="https://fonts.googleapis.com/css2?family=Cinzel:wght@700&family=Montserrat:wght@500;600;700&family=Arimo:wght@400&display=swap">
<style>
  :root {
    --stage: #000000;
    --card: #ffffff;
    --brand-green: #5c9a1f;
    --panel-light: #ffffff;
    --panel-tint: #e9f3e1;
    --ink: #111111;
    --label: #ffffff;
  }
  html, body {
    margin: 0;
    padding: 0;
    width: 1031px;
    height: 1200px;
    overflow: hidden;
    background: var(--stage);
  }
  .presentation {
    display: block;
    width: 1031px;
    height: 1200px;
  }
  .card-face { fill: var(--card); }
  .frame-line {
    stroke: var(--brand-green);
    stroke-width: 3;
    fill: none;
  }
  .side-label {
    font-family: "Cinzel", serif;
    font-weight: 700;
    fill: var(--label);
  }
  .brand-name {
    font-family: "Montserrat", sans-serif;
    font-weight: 600;
    font-size: 54px;
    letter-spacing: 6px;
    fill: var(--brand-green);
  }
  .brand-slogan {
    font-family: "Montserrat", sans-serif;
    font-weight: 500;
    font-size: 16.5px;
    letter-spacing: 2.4px;
    fill: var(--ink);
  }
  .holder-name {
    font-family: "Montserrat", sans-serif;
    font-weight: 700;
    font-size: 30px;
    fill: var(--ink);
  }
  .holder-role {
    font-family: "Montserrat", sans-serif;
    font-weight: 700;
    font-size: 20px;
    fill: var(--ink);
  }
  .contact-key {
    font-family: "Cinzel", serif;
    font-weight: 700;
    font-size: 11px;
    fill: var(--ink);
  }
  .contact-value {
    font-family: "Arimo", sans-serif;
    font-size: 10px;
    fill: var(--ink);
  }
</style>
</head>
<body>
<svg class="presentation" viewBox="0 0 900 1048" preserveAspectRatio="none" xmlns="http://www.w3.org/2000/svg">
  <defs>
    <radialGradient id="panelGlow" cx="50%" cy="50%" r="60%">
      <stop offset="0%" stop-color="var(--panel-light)"/>
      <stop offset="100%" stop-color="var(--panel-tint)"/>
    </radialGradient>
  </defs>

  <!-- Front of card -->
  <g class="card card--front">
    <rect class="card-face" x="88" y="157" width="552" height="365"/>
    <rect class="brand-panel" x="126" y="202" width="481" height="278" fill="url(#panelGlow)"/>
    <path class="frame-line" d="M131 171 H96 V219"/>
    <path class="frame-line" d="M155 171 H614"/>
    <path class="frame-line" d="M123 511 H573"/>
    <path class="frame-line" d="M594 511 H629 V462"/>
    <text class="brand-name" x="363" y="357" text-anchor="middle">RENEWA</text>
    <text class="brand-slogan" x="363" y="385" text-anchor="middle">MAKING TECHNOLOGY EASIER</text>
  </g>
  <text class="side-label" x="670" y="318" font-size="42">Front</text>

  <!-- Back of card -->
  <g class="card card--back">
    <rect class="card-face" x="283" y="547" width="554" height="360"/>
    <path class="frame-line" d="M330 560 H294 V608"/>
    <path class="frame-line" d="M355 558 H788"/>
    <path class="frame-line" d="M338 894 H772"/>
    <path class="frame-line" d="M793 895 H828 V847"/>
    <text class="holder-name" x="566" y="693" text-anchor="middle">YOUR NAME HERE</text>
    <text class="holder-role" x="575" y="725" text-anchor="middle">YOUR POSITION</text>
    <text x="345" y="784"><tspan class="contact-key">Email :</tspan><tspan class="contact-value"> yourname@xxx.com</tspan></text>
    <text x="345" y="799"><tspan class="contact-key">Web</tspan><tspan class="contact-value"> : www.websitename.com</tspan></text>
    <text x="665" y="795"><tspan class="contact-key">Phone :</tspan><tspan class="contact-value"> 00-11-222-3333</tspan></text>
    <text x="665" y="810"><tspan class="contact-key">Fax:</tspan><tspan class="contact-value"> 00-11-222-3333</tspan></text>
  </g>
  <text class="side-label" x="105" y="735" font-size="42">Back</text>
</svg>
</body>
</html>
```